Business Card for Canvas Lotus-Eco Friendly Organic Clothing Brand

We are looking for an amazing business card for our eco friendly, organic clothing brand. We are thinking maybe a business card with a peel off sticker on the back, since our hanging clothing tag is a peel off sticker on the back. I will attach our hang tag so we can make sure we stay in line with our design. I've also attached a bag we are doing because I do like the scattered emblem look as well.

```html
<!DOCTYPE html>
<html lang="en">
<head>
<meta charset="utf-8">
<title>Canvas Lotus – Business Card</title>
<link rel="stylesheet" href="https://fonts.googleapis.com/css2?family=Open+Sans:wght@400;600;700&display=swap">
<style>
  :root {
    --page-bg: #ece8e1;
    --gold: #c9a440;
    --gold-deep: #b8922e;
    --gold-light: #f3e3b0;
    --gold-glow: #fbf1d2;
    --ink: #333333;
    --ink-soft: #4a4a4a;
    --white: #ffffff;
    --tag-dark: #1f241a;
    --tag-mid: #3a4230;
  }
  * { margin: 0; padding: 0; box-sizing: border-box; }
  html, body {
    width: 1200px; height: 900px; overflow: hidden;
    background: var(--page-bg);
    font-family: "Open Sans", sans-serif;
  }
  .canvas { position: relative; width: 1200px; height: 900px; }

  .card {
    position: absolute;
    width: 620px; height: 354px;
    border-radius: 4px;
    box-shadow: 0 10px 30px rgba(0,0,0,0.18);
    overflow: hidden;
  }

  /* Front */
  .card-front {
    left: 90px; top: 90px;
    background: var(--gold);
  }
  .front-glow {
    position: absolute; inset: 0;
    background: radial-gradient(circle at 50% 48%, var(--gold-glow) 0%, var(--gold-light) 22%, var(--gold) 55%, var(--gold-deep) 100%);
  }
  .front-brand {
    position: absolute; left: 0; right: 0; top: 138px;
    text-align: center; color: var(--white);
    font-weight: 700; font-size: 40px; letter-spacing: 0.5px;
  }
  .front-url {
    position: absolute; left: 0; right: 0; top: 218px;
    text-align: center; color: var(--white);
    font-weight: 400; font-size: 17px; letter-spacing: 0.5px;
  }

  /* Back */
  .card-back {
    left: 490px; top: 440px;
    background: var(--white);
  }
  .contact {
    position: absolute; left: 370px; top: 34px;
  }
  .contact-name {
    font-weight: 600; font-size: 21px; color: var(--ink);
  }
  .contact-title {
    font-size: 12px; color: var(--gold); margin-bottom: 14px;
  }
  .contact-list { list-style: none; }
  .contact-list li {
    display: flex; align-items: center; gap: 8px;
    font-size: 13px; color: var(--ink-soft); line-height: 21px;
  }
  .contact-list svg { width: 12px; height: 12px; fill: var(--gold); flex: none; }

  .hang-tag {
    position: absolute; left: 40px; top: 218px;
    width: 290px; height: 104px;
  }
  .tag-body {
    position: absolute; left: 40px; top: 8px;
    width: 250px; height: 88px;
    border-radius: 12px;
    background: linear-gradient(135deg, var(--tag-mid), var(--tag-dark));
    border: 2px solid var(--gold);
  }
  .tag-hole {
    position: absolute; right: 12px; top: 10px;
    width: 8px; height: 8px; border-radius: 50%;
    background: var(--white);
  }
  .tag-brand {
    position: absolute; left: 70px; top: 20px;
    font-weight: 700; font-size: 22px; color: var(--gold);
  }
  .tag-url {
    position: absolute; left: 80px; top: 58px;
    font-size: 9px; color: var(--gold-light);
  }
  .tag-emblem {
    position: absolute; left: 8px; top: 14px;
    width: 76px; height: 76px;
    transform: rotate(-18deg);
    border: 2px solid var(--gold);
    background: radial-gradient(circle, var(--gold-light), var(--tag-mid) 80%);
  }
</style>
</head>
<body>
<main class="canvas">

  <section class="card card-front">
    <div class="front-glow" role="img" aria-label="Soft golden glow where the seated meditation emblem sits"></div>
    <div class="front-brand">Canvas Lotus</div>
    <div class="front-url">www.canvaslotus.com</div>
  </section>

  <section class="card card-back">
    <div class="contact">
      <div class="contact-name">Daniel Reyes</div>
      <div class="contact-title">Managing Director</div>
      <ul class="contact-list">
        <li><svg viewBox="0 0 12 12"><path d="M2 1h2l1 3-1.5 1a6 6 0 0 0 3 3L7.5 6.5l3 1v2A1.5 1.5 0 0 1 9 11 8 8 0 0 1 1 3 1.5 1.5 0 0 1 2 1z"/></svg>044-456-7890</li>
        <li><svg viewBox="0 0 12 12"><rect x="3" y="1" width="6" height="3"/><rect x="1" y="4" width="10" height="5" rx="1"/><rect x="3" y="8" width="6" height="3"/></svg>123-456-7890</li>
        <li><svg viewBox="0 0 12 12"><rect x="3" y="0.5" width="6" height="11" rx="1"/><rect x="4" y="2" width="4" height="6" fill="#fff"/></svg>123-456-7890</li>
        <li><svg viewBox="0 0 12 12"><rect x="1" y="2.5" width="10" height="7" rx="1"/><path d="M1.5 3l4.5 3.5L10.5 3" fill="none" stroke="#fff" stroke-width="1"/></svg>info@youremail.com</li>
        <li><svg viewBox="0 0 12 12"><path d="M4 8l4-4" stroke="#c9a440" stroke-width="1.4"/><path d="M5 3l1.5-1.5a2 2 0 0 1 3 3L8 6M7 9l-1.5 1.5a2 2 0 0 1-3-3L4 6" fill="none" stroke="#c9a440" stroke-width="1.4"/></svg>www.website.com</li>
      </ul>
    </div>

    <div class="hang-tag">
      <div class="tag-body" role="img" aria-label="Hang tag sticker with dark camouflage pattern">
        <span class="tag-hole"></span>
        <span class="tag-brand">Canvas Lotus</span>
        <span class="tag-url">www.canvaslotus.com</span>
      </div>
      <div class="tag-emblem" role="img" aria-label="Gold camouflage meditation emblem"></div>
    </div>
  </section>

</main>
</body>
</html>
```